Schriftdesign für Shop-Header Bild (Schmuckhandel) / Online-Marketing Material
Wir verkaufen Schmuck im Onlineshop mit Herz
Wir benötigen den vorgegebenen Text in schöner Form, Farbe und Größe harmonisch eingefügt, in unserem Bild.
Folgender Text soll sich schick ins Bild einfügen oder in 3-D vielleicht in Schriftfarbe gold hervorheben:
Mit ganzem Herzen für Sie da!
Ihr Online -Juwelier mit Herz
Siehe auch unser altes Bild mit Text, im Shop, wie es nicht aussehen sollte: www.sonnenflocke.de

```html
<!DOCTYPE html>
<html lang="de">
<head>
<meta charset="utf-8">
<title>Shop-Header – Online-Juwelier mit Herz</title>
<link rel="stylesheet" href="https://fonts.googleapis.com/css2?family=Abril+Fatface&display=swap">
<style>
  :root {
    --page: #ecebe8;
    --satin-light: #fbfaf8;
    --satin-mid: #eeedf0;
    --satin-shade: #dedcdc;
    --gold-light: #ffe27a;
    --gold: #e3a91f;
    --gold-deep: #a8700c;
    --gold-dark: #6e4605;
    --shadow: rgba(70, 50, 20, 0.35);
  }
  * { margin: 0; padding: 0; box-sizing: border-box; }
  html, body {
    width: 1200px; height: 513px; overflow: hidden;
    background: var(--page);
  }
  .header-banner {
    position: absolute; left: 0; top: 103px;
    width: 1200px; height: 307px; overflow: hidden;
    background:
      radial-gradient(ellipse 60% 80% at 70% 60%, var(--satin-light), transparent 70%),
      linear-gradient(160deg, var(--satin-mid) 0%, var(--satin-light) 45%, var(--satin-shade) 100%);
  }
  .pendant-photo {
    position: absolute;
    background: radial-gradient(circle at 40% 35%, var(--gold-light), var(--gold) 45%, var(--gold-deep) 85%);
  }
  .pendant-photo--left {
    left: 0; top: 0; width: 254px; height: 307px;
    border-radius: 0 48% 46% 0 / 0 40% 60% 0;
  }
  .pendant-photo--top {
    left: 905px; top: -40px; width: 194px; height: 125px;
    border-radius: 10% 10% 50% 50% / 10% 10% 90% 90%;
  }
  .pendant-photo--bottom {
    left: 488px; top: 215px; width: 172px; height: 120px;
    border-radius: 50% 50% 10% 10% / 70% 70% 10% 10%;
  }
  .headline {
    position: absolute; left: 256px; top: 72px; width: 920px;
    font-family: "Abril Fatface", serif;
    font-size: 59px; line-height: 70px; text-align: center;
    white-space: nowrap;
    filter: drop-shadow(2px 3px 0 var(--gold-dark)) drop-shadow(3px 6px 5px var(--shadow));
  }
  .headline__line {
    display: block;
    background: linear-gradient(180deg, var(--gold-light) 0%, var(--gold) 50%, var(--gold-deep) 100%);
    -webkit-background-clip: text; background-clip: text;
    color: transparent;
  }
</style>
</head>
<body>
  <header class="header-banner">
    <div class="pendant-photo pendant-photo--left" role="img" aria-label="Goldene Herzanhänger an feiner Kette auf weißem Satin"></div>
    <div class="pendant-photo pendant-photo--top" role="img" aria-label="Goldener Herzanhänger, angeschnitten am oberen Rand"></div>
    <div class="pendant-photo pendant-photo--bottom" role="img" aria-label="Goldener Herzanhänger mit Kette, angeschnitten am unteren Rand"></div>
    <h1 class="headline">
      <span class="headline__line">Mit ganzem Herzen für Sie da!</span>
      <span class="headline__line">Ihr Online - Juwelier mit Herz</span>
    </h1>
  </header>
</body>
</html>
```